Stationary Design For Youthful Disability Company

Hi Designers,
Looking to have our brand applied to a range of stationary items to professionalise our approach, we are a disability services company that aligns young carers with disabled youth and adults. Our stationary needs to look professional but can verge into a fun bright territory too.
Winning designer will be first contact for advertising campaign, form creation and web-design in January 2014.
Cheers,
Tom
Brightpath Disability Services
Design Briefs
Stationary.
Sleek fun and bright stationary that portrays a professional but youthful disability service. Company prides its self on delivering youthful carers to disabled clients.
Needed:
- Business Card - Letter Head - Email Signature
- Invoice / Quotation (blank branded paper) - Normal Envelope - A4 Envelope
- Stationary for future forms or documents. (Doesn't need to include all contacts, branding is enough).
Would be nice if we were able to edit numbers etc as we change them.
Include:
Marcus Ferrow - Managing Director
M. 0472 915 408
E. mferrow@brightpathcare.example
A. PO Box 71 Kelsdale 3152
ABN. 58392046115

```html
<!DOCTYPE html>
<html lang="en">
<head>
<meta charset="utf-8">
<title>Brightpath Disability Services – Stationery Set</title>
<link href="https://fonts.googleapis.com/css2?family=Open+Sans:wght@400;600;700;800&family=Arimo:wght@400;700&display=swap" rel="stylesheet">
<style>
:root{
  --board:#dedede;
  --paper:#ffffff;
  --paper-edge:#f2f2f2;
  --ink:#8a8a8a;
  --ink-dark:#666;
  --rule:#9a9a9a;
  --brand:#2a8fc9;
  --lime:#c6dc2a;
  --violet:#7b5aa6;
  --blue:#1a8ac6;
  --orange:#f28c1e;
  --crimson:#c0244a;
  --mail-bar:#eef1f5;
  --mail-line:#c9d0d8;
}
*{box-sizing:border-box;margin:0;padding:0}
html,body{width:1200px;height:1000px;overflow:hidden;background:var(--board)}
body{position:relative;font-family:"Open Sans",Arial,sans-serif;color:var(--ink)}
.sheet{position:absolute;background:linear-gradient(160deg,var(--paper) 0%,var(--paper-edge) 100%);box-shadow:0 2px 5px rgba(0,0,0,.28);overflow:hidden}

/* brand wordmark */
.wordmark{position:absolute;display:flex;align-items:center;gap:4px;font-weight:800;color:var(--brand);line-height:1;white-space:nowrap}
.wordmark .dot{border-radius:50%;background:var(--brand);flex:none}
.wordmark small{display:block;font-size:.45em;font-weight:800;letter-spacing:.02em}

.sender{position:absolute;font-size:6.5px;line-height:9px;font-weight:600;color:var(--ink)}
.faint-art{position:absolute;left:0;right:0;bottom:0}

/* letterhead */
.letterhead{left:47px;top:141px;width:356px;height:504px}
.letter-body{position:absolute;left:43px;top:122px;width:266px;font-size:6.6px;line-height:12.4px;font-weight:700;color:#8d8d8d;text-align:justify}
.letter-body p{margin-bottom:12.4px}
.letter-body .greeting{margin-bottom:10px}
.signature{position:absolute;left:50px;top:340px;width:70px;height:40px;background:rgba(120,120,120,.08);border-radius:4px}

/* invoice */
.invoice{left:424px;top:141px;width:356px;height:504px}
.field{position:absolute;font-size:7px;color:var(--ink)}
.field .blank{display:inline-block;border-bottom:1px solid var(--rule);vertical-align:bottom;margin-left:3px}
.ledger{position:absolute;left:49px;top:122px;width:262px;height:291px;border:1px solid var(--rule)}
.ledger-head{height:18px;border-bottom:1px solid var(--rule);display:flex;justify-content:space-between;padding:0 7px 0 14px;font-size:8.5px;line-height:18px;letter-spacing:.05em;color:#777}
.ledger-total{position:absolute;left:0;right:0;bottom:0;height:16px;border-top:1px solid var(--rule);padding-left:14px;font-size:8.5px;line-height:17px;letter-spacing:.05em;color:#777}

/* A4 envelope */
.a4-flap{position:absolute;left:803px;top:88px;width:356px;height:54px}
.a4-envelope{left:802px;top:141px;width:357px;height:504px}
.a4-envelope .colour-field{position:absolute;right:0;top:0;width:200px;height:504px}

/* DL envelopes */
.dl-back{left:47px;top:674px;width:356px;height:165px}
.dl-front{left:424px;top:674px;width:356px;height:165px}

/* business cards */
.card-front{left:802px;top:671px;width:153px;height:85px}
.card-back{left:1006px;top:671px;width:153px;height:85px}
.card-details{position:absolute;left:72px;top:21px;font-size:7.5px;line-height:8px;font-weight:700;color:#b8b8b8}
.card-details .name{margin-bottom:4px;font-size:7.6px}

/* email */
.email{left:802px;top:768px;width:357px;height:193px;background:var(--paper);font-family:Arimo,Arial,sans-serif}
.mail-toolbar{height:15px;background:var(--mail-bar);border-bottom:1px solid var(--mail-line);font-size:5.5px;line-height:15px;padding-left:5px;color:#335}
.mail-fields{position:absolute;left:8px;top:18px;right:8px;font-size:5px;color:#334}
.mail-row{height:11px;display:flex;align-items:center;margin-bottom:2px}
.mail-row .label{width:27px}
.mail-row .input{flex:1;height:9px;border:1px solid var(--mail-line);padding-left:2px;line-height:8px}
.suggest{position:absolute;left:44px;top:28px;background:#fffbe0;border:1px solid #b9b18a;font-size:4.5px;line-height:6px;padding:0 2px;color:#335}
.mail-format{position:absolute;left:0;right:0;top:56px;height:11px;background:var(--mail-bar);border-top:1px solid var(--mail-line);border-bottom:1px solid var(--mail-line);font-size:5px;line-height:10px;padding-left:6px;color:#333}
.mail-body{position:absolute;left:6px;top:74px;font-size:7px;line-height:9px;color:#111}
.mail-body p{margin-bottom:7px}
.mail-body .sign{margin-top:20px}
.mail-body .addr{font-family:"Open Sans",Arial,sans-serif;font-size:5.5px;line-height:8px;color:#777}
</style>
</head>
<body>

<!-- Letterhead -->
<section class="sheet letterhead">
  <div class="sender" style="left:46px;top:42px">Brightpath<br>PO Box 71<br>Kelsdale 3152</div>
  <div class="wordmark" style="left:226px;top:45px;font-size:11px"><span class="dot" style="width:7px;height:7px"></span><span>BRIGHTPATH<small>DISABILITY SERVICES</small></span></div>
  <div class="letter-body">
    <p class="greeting">Dear Mrs Hale</p>
    <p>Lorem ipsum dolor sit amet, consectetur adipisicing elit, sed do eiusmod tempor incididunt ut labore et dolore magna aliqua. Ut enim ad minim veniam, quis nostrud exercitation ullamco laboris nisi ut aliquip ex ea commodo consequat. Duis aute irure dolor in reprehenderit in voluptate velit esse cillum dolore eu fugiat nulla pariatur. Excepteur sint occaecat cupidatat non proident, sunt in culpa qui officia deserunt mollit anim id est laborum.<br>Lorem ipsum dolor sit amet, consectetur adipisicing elit, sed do eiusmod tempor incididunt ut labore et dolore magna aliqua. Ut enim ad minim veniam, quis nostrud exercitation ullamco laboris nisi ut aliquip ex ea commodo consequat.</p>
    <p>Lorem ipsum dolor sit amet, consectetur adipisicing elit, sed do eiusmod tempor incididunt ut labore et dolore magna aliqua. Ut enim ad minim veniam, quis nostrud exercitation ullamco laboris nisi ut aliquip ex ea commodo consequat.</p>
    <p>Sincerely,</p>
  </div>
  <div class="signature" role="img" aria-label="Handwritten signature"></div>
  <div class="faint-art" role="img" aria-label="Faint oversized brand symbol decoration in soft grey, lime, violet and blue" style="height:200px;background:linear-gradient(180deg,rgba(220,220,220,0) 0%,rgba(215,215,220,.55) 45%,rgba(205,215,195,.6) 65%,rgba(200,190,215,.6) 82%,rgba(180,210,225,.65) 100%)"></div>
</section>

<!-- Invoice / quotation -->
<section class="sheet invoice">
  <div class="sender" style="left:49px;top:42px">Brightpath<br>PO Box 71<br>Kelsdale 3152</div>
  <div class="wordmark" style="left:228px;top:45px;font-size:11px"><span class="dot" style="width:7px;height:7px"></span><span>BRIGHTPATH<small>DISABILITY SERVICES</small></span></div>
  <div class="field" style="left:49px;top:97px;font-size:6px">Supplier<span class="blank" style="width:58px"></span></div>
  <div class="field" style="left:212px;top:99px">Supplier<span class="blank" style="width:66px"></span></div>
  <div class="faint-art" role="img" aria-label="Faint oversized brand symbol decoration in soft grey, pink, peach and blue" style="height:240px;background:linear-gradient(180deg,rgba(220,220,220,0) 0%,rgba(215,215,218,.5) 40%,rgba(225,195,205,.55) 68%,rgba(235,210,190,.55) 85%,rgba(185,215,228,.65) 100%)"></div>
  <div class="ledger">
    <div class="ledger-head"><span>Item</span><span>Amount</span></div>
    <div class="ledger-total">Total</div>
  </div>
  <div class="field" style="left:51px;top:434px;font-size:8.5px;letter-spacing:.04em">Supplier<span class="blank" style="width:84px"></span></div>
</section>

<!-- A4 envelope -->
<svg class="a4-flap" viewBox="0 0 356 54" aria-hidden="true">
  <defs><linearGradient id="flapLime" x1="0" y1="0" x2="1" y2="0"><stop offset="0" stop-color="#a8c62c"/><stop offset="1" stop-color="#d6e41e"/></linearGradient></defs>
  <polygon points="0,54 46,2 310,2 356,54" fill="url(#flapLime)"/>
</svg>
<section class="sheet a4-envelope">
  <div class="colour-field" role="img" aria-label="Brand symbol pattern in lime, violet, blue, orange and crimson running down the right edge" style="background:linear-gradient(180deg,rgba(198,220,42,.55) 0%,rgba(123,90,166,.45) 30%,rgba(26,138,198,.5) 52%,rgba(242,140,30,.45) 72%,rgba(192,36,74,.5) 100%);-webkit-mask:linear-gradient(90deg,transparent 0%,#000 60%);mask:linear-gradient(90deg,transparent 0%,#000 60%)"></div>
</section>

<!-- DL envelope, back -->
<section class="sheet dl-back">
  <div role="img" aria-label="Large grey brand symbol across the envelope back" style="position:absolute;left:20px;top:0;width:316px;height:165px;background:radial-gradient(ellipse at 50% 40%,rgba(140,140,140,.75) 0%,rgba(170,170,170,.55) 55%,rgba(200,200,200,0) 80%)"></div>
  <svg style="position:absolute;left:0;top:0" width="356" height="45" viewBox="0 0 356 45" aria-hidden="true">
    <polygon points="0,0 356,0 330,42 30,42" fill="#fff"/>
  </svg>
</section>

<!-- DL envelope, front -->
<section class="sheet dl-front">
  <div class="wordmark" style="left:122px;top:67px;font-size:16px"><span class="dot" style="width:10px;height:10px"></span><span>BRIGHTPATH</span></div>
</section>

<!-- Business card, front -->
<section class="sheet card-front">
  <div class="wordmark" style="left:34px;top:34px;font-size:11px"><span class="dot" style="width:7px;height:7px"></span><span>BRIGHTPATH<small>DISABILITY SERVICES</small></span></div>
</section>

<!-- Business card, back -->
<section class="sheet card-back">
  <span style="position:absolute;left:28px;top:34px;width:14px;height:14px;border-radius:50%;background:#cfcfcf"></span>
  <div class="card-details">
    <div class="name">Alan Reed</div>
    0472 915<br>areed@bright<br>path.example<br>Kelsdale 3152
  </div>
</section>

<!-- Email signature -->
<section class="sheet email">
  <div class="mail-toolbar">Send &nbsp;▪ &nbsp;▪ &nbsp;▪ &nbsp;▪ &nbsp;! &nbsp;↓ &nbsp;▪ &nbsp;▪ &nbsp;Options... &nbsp;&nbsp;HTML</div>
  <div class="mail-fields">
    <div class="mail-row"><span class="label">To...</span><span class="input">leo</span></div>
    <div class="mail-row"><span class="label">Cc...</span><span class="input"></span></div>
    <div class="mail-row"><span class="label">Subject:</span><span class="input">Next Week</span></div>
  </div>
  <div class="suggest">leonb@northgate.example<br>Leon Barker [leon.barker@northgate.example]</div>
  <div class="mail-format">Arial &nbsp;&nbsp;&nbsp;&nbsp;&nbsp;&nbsp;&nbsp;&nbsp;&nbsp;&nbsp;&nbsp;&nbsp;&nbsp;&nbsp;&nbsp;&nbsp;&nbsp;&nbsp;&nbsp;&nbsp; 12 &nbsp; <b>B</b> <i>I</i> <u>U</u> &nbsp;≡ ≡ &nbsp;A</div>
  <div class="mail-body">
    <p>Hi Leon,</p>
    <p>Back to school already! Do you have time to go through the ICT plan today?</p>
    <p>Thanks,</p>
    <div class="sign">Nadia</div>
    <div class="addr">PO Box 71<br>Kelsdale 3152</div>
  </div>
  <div class="wordmark" style="left:7px;top:166px;font-size:11px"><span class="dot" style="width:7px;height:7px"></span><span>BRIGHTPATH<small>DISABILITY SERVICES</small></span></div>
</section>

</body>
</html>
```